New design for www.TrimTable.com

On TrimTable you can find & book your hairdresser. TrimTable is the biggest platform in the Netherlands.

- The design should be a responcive design
- Should be able to go global, should fit in perfectly between all the big booking platforms like stayvo, ridlo etc,
- Should have te result of more bookings. :)
- We are ‘only’ asking a beautiful design, not a technical solution.
- We need a homepage (https://trimtable.com/), search resultpage ((https://trimtable.com/kapper/amsterdam/#), salonpage (https://trimtable.com/kapper/vorden/lumo-for-hair/), about us page (https://trimtable.com/aboutus/), for the hairdresser info page (https://trimtable.com/kapper/), login/register page (https://trimtable.com/account/signin/).

- On the page of the hairdresser there is a dynamic part. The part where you create your appointment. Please take a look at this part too after you choose your treatment (behandeling), employee (medewerker), Date (datum) and time (tijd). The part that you see after this, is the part where you fill in your data as a consumer.

I've added more logo's but mostly we use the green color.

A few of our competitors: www.plumsalo.com, www.korifex.com

Target Market(s)

All consumers

Industry/Entity Type

Hair And Beauty

Number of Pages Required

5+ page

Font styles to use
Sans Serif

Colors
abd036
c3c3c3
757575

Requirements
Must have
• Responsive
• We did an A/B test with the homepage. It turns out that option B works better then option A (take a look at the uploaded pictures). So what we need on the homepage: The USP's with the green checkboxes, The search button needs to by dynamic (changes for example from light green to dark green so you can see you can click it) The call to action sentence Zoek & Vind je kapsalon, the searchfield and searchbutton should be seperated.
Nice to have
• The style that we like is the flat design style. The website should be simple, clean and it should feel a bit like a luxury thing. Because an appointment with the hairdresser can be a real treat and luxury moment for yourself.
• The luxury feeling and flat design that is in the www.ridlo.com website is really nice for example. But then it has to be a bit more light and not so black and dark.

```html
<!DOCTYPE html>
<html lang="en">
<head>
<meta charset="utf-8">
<title>TrimTable – Find &amp; book your hairdresser</title>
<link href="https://fonts.googleapis.com/css2?family=Oswald:wght@400;500;600&family=Open+Sans:wght@400;600;700&display=swap" rel="stylesheet">
<style>
:root{
  --green:#8cc63f;
  --green-dark:#6fa22a;
  --orange:#f7941d;
  --orange-dark:#e9820c;
  --ink:#333333;
  --grey:#757575;
  --light:#c3c3c3;
  --panel:#eeeeee;
  --footer-bar:#3a3a3a;
  --white:#ffffff;
}
*{box-sizing:border-box;margin:0;padding:0}
html,body{width:874px;height:1200px;overflow:hidden;background:var(--white)}
body{position:relative;font-family:"Open Sans",Arial,sans-serif;color:var(--ink)}
.heading{font-family:"Oswald",Arial,sans-serif;text-transform:uppercase}

/* hero */
.hero{position:absolute;left:0;top:0;width:874px;height:458px;overflow:hidden}
.hero-photo{position:absolute;inset:0;background:linear-gradient(120deg,#5d5a55 0%,#8a847a 35%,#6e675d 60%,#4b4844 100%)}
.hero-shade{position:absolute;inset:0;background:rgba(20,20,20,.45)}
.menu-btn{position:absolute;right:22px;top:14px;width:34px;height:28px;background:var(--green);border-radius:3px;padding:8px 9px;display:flex;flex-direction:column;justify-content:space-between}
.menu-btn span{display:block;height:2px;background:var(--white)}
.brand{position:absolute;top:106px;left:0;width:100%;display:flex;justify-content:center;align-items:center;gap:10px}
.brand-dot{width:40px;height:40px;border-radius:50%;background:var(--white)}
.brand-name{font-family:"Open Sans",Arial,sans-serif;font-weight:700;font-size:34px;color:var(--white);letter-spacing:-.5px}
.hero-title{position:absolute;top:222px;width:100%;text-align:center;color:var(--white);font-size:31px;font-weight:500;letter-spacing:.5px}
.hero-sub{position:absolute;top:266px;width:100%;text-align:center;color:var(--white);font-size:15px;letter-spacing:1.5px}
.search{position:absolute;top:300px;left:247px;width:218px;height:36px;display:flex}
.search-field{flex:1;background:var(--white);font-size:11px;color:#999;padding:11px 10px}
.search-btn{width:40px;background:var(--green);display:flex;align-items:center;justify-content:center}
.book{position:absolute;top:300px;left:492px;height:36px;display:flex}
.book-icon{width:38px;background:var(--green-dark);display:flex;align-items:center;justify-content:center}
.book-label{background:var(--green);color:var(--white);font-size:16px;padding:7px 16px;letter-spacing:.5px}

/* services */
.services{position:absolute;top:458px;left:0;width:874px;height:150px;background:var(--panel);display:grid;grid-template-columns:repeat(5,1fr);padding:0 30px}
.service{text-align:center;padding-top:34px}
.service-icon{width:44px;height:44px;margin:0 auto 10px;display:block}
.service-title{font-size:12px;color:var(--ink);letter-spacing:.3px}
.service-text{font-size:8px;color:var(--grey);line-height:1.4;margin-top:6px;padding:0 18px}

/* welcome */
.welcome-photo{position:absolute;left:48px;top:632px;width:320px;height:305px;border-radius:0 150px 150px 0;background:linear-gradient(135deg,#8b5a3a 0%,#c4946a 45%,#e8d2bd 100%)}
.welcome{position:absolute;left:412px;top:636px;width:420px}
.welcome-head{display:flex;align-items:center;gap:12px}
.welcome-kicker{font-size:30px;color:var(--ink);letter-spacing:1px}
.welcome-name{display:flex;align-items:center;gap:10px;margin-top:2px}
.welcome-name .heading{font-size:32px;color:var(--green);letter-spacing:1px;font-weight:500}
.welcome-rule{flex:1;height:1px;background:var(--light)}
.welcome-text{margin-top:22px;font-size:9.5px;line-height:1.55;color:var(--grey)}
.cta{display:inline-block;margin-top:40px;background:var(--green);color:var(--white);font-size:14px;padding:8px 22px;letter-spacing:.5px}

/* footer */
.footer{position:absolute;left:0;top:992px;width:874px;height:174px;background:var(--orange);color:var(--white)}
.col{position:absolute;top:18px}
.col-title{font-size:13px;letter-spacing:.5px;margin-bottom:10px}
.col-title b{font-weight:500;color:#3a3a3a}
.links{list-style:none;font-size:9px;line-height:16px}
.links li::before{content:"›";margin-right:6px}
.contact-row{display:flex;gap:7px;font-size:9px;line-height:1.4;margin-bottom:8px}
.contact-row svg{flex:none;margin-top:1px}
.gallery{display:grid;grid-template-columns:38px 38px;gap:5px}
.gallery span{height:28px;background:linear-gradient(135deg,#7a5236,#c59a72)}
.view-all{font-size:9px;margin-top:6px;display:block;text-align:right;width:81px}
.hours{font-size:9px;display:grid;grid-template-columns:54px auto;row-gap:9px}
.hours dt{font-family:"Oswald",Arial,sans-serif;font-size:11px}
.footer-brand{position:absolute;left:505px;top:128px;display:flex;align-items:center;gap:7px}
.footer-brand .brand-dot{width:26px;height:26px}
.footer-brand .brand-name{font-size:22px}
.device{position:absolute;left:706px;top:882px;width:138px;height:282px;border-radius:20px;background:linear-gradient(180deg,#2d2d2d,#1a1a1a)}
.bottom-bar{position:absolute;left:0;top:1166px;width:874px;height:34px;background:var(--footer-bar);color:#bbb;font-size:9px;padding:11px 36px}
.social{position:absolute;right:32px;top:8px;display:flex;gap:6px}
.social span{width:18px;height:18px;border-radius:50%;border:1px solid #888}
</style>
</head>
<body>

<header class="hero">
  <div class="hero-photo" role="img" aria-label="Hair salon interior with stylists cutting hair"></div>
  <div class="hero-shade"></div>
  <div class="menu-btn"><span></span><span></span><span></span></div>
  <div class="brand"><span class="brand-dot"></span><span class="brand-name">TrimTable</span></div>
  <h1 class="hero-title heading">The greatest hair dresser booking site</h1>
  <p class="hero-sub heading">We give you the look that matters</p>
  <div class="search">
    <div class="search-field">Select a service, city or salon</div>
    <div class="search-btn"><svg width="16" height="16" viewBox="0 0 16 16"><circle cx="6.5" cy="6.5" r="4.5" fill="none" stroke="#fff" stroke-width="2"/><path d="M10 10l4.5 4.5" stroke="#fff" stroke-width="2.2"/></svg></div>
  </div>
  <div class="book">
    <div class="book-icon"><svg width="18" height="18" viewBox="0 0 18 18"><rect x="2" y="3" width="14" height="13" rx="1" fill="none" stroke="#fff" stroke-width="1.8"/><path d="M2 7h14M6 1v4M12 1v4" stroke="#fff" stroke-width="1.8"/></svg></div>
    <div class="book-label heading">Book an appointment</div>
  </div>
</header>

<section class="services">
  <div class="service">
    <svg class="service-icon" viewBox="0 0 44 44"><circle cx="14" cy="31" r="5" fill="none" stroke="#f7941d" stroke-width="2.5"/><circle cx="30" cy="31" r="5" fill="none" stroke="#f7941d" stroke-width="2.5"/><path d="M17 27L32 8M27 27L12 8" stroke="#f7941d" stroke-width="2.5"/></svg>
    <div class="service-title heading">Cutting and styling</div>
    <p class="service-text">Fresh cuts and styling by skilled local pros near you</p>
  </div>
  <div class="service">
    <svg class="service-icon" viewBox="0 0 44 44"><rect x="15" y="14" width="14" height="24" rx="3" fill="#f7941d"/><rect x="18" y="6" width="8" height="8" fill="#f7941d"/></svg>
    <div class="service-title heading">Hair color</div>
    <p class="service-text">Rich colours, highlights and tints for every hair type</p>
  </div>
  <div class="service">
    <svg class="service-icon" viewBox="0 0 44 44"><path d="M22 6C16 16 12 22 12 28a10 10 0 0020 0c0-6-4-12-10-22z" fill="#f7941d"/></svg>
    <div class="service-title heading">Hair treatment</div>
    <p class="service-text">Care treatments that repair and restore shine</p>
  </div>
  <div class="service">
    <svg class="service-icon" viewBox="0 0 44 44"><rect x="10" y="8" width="24" height="28" rx="12" fill="#f7941d"/><rect x="16" y="24" width="12" height="3" fill="#eeeeee"/></svg>
    <div class="service-title heading">Beard treatment</div>
    <p class="service-text">Trims, shaves and shaping for a sharp beard</p>
  </div>
  <div class="service">
    <svg class="service-icon" viewBox="0 0 44 44"><circle cx="22" cy="22" r="14" fill="#f7941d"/><path d="M15 22l5 5 9-10" fill="none" stroke="#fff" stroke-width="3"/></svg>
    <div class="service-title heading">The finish</div>
    <p class="service-text">Blow dry and final touches to complete your look</p>
  </div>
</section>

<div class="welcome-photo" role="img" aria-label="Two portraits of women with glossy styled hair, framed in a large letter shape"></div>
<section class="welcome">
  <div class="welcome-head">
    <svg width="34" height="42" viewBox="0 0 34 42"><path d="M17 1C8 1 2 8 2 16c0 11 15 25 15 25s15-14 15-25C32 8 26 1 17 1z" fill="#8cc63f"/><circle cx="17" cy="16" r="7" fill="#fff"/></svg>
    <span class="welcome-kicker heading">Welcome to</span>
  </div>
  <div class="welcome-name">
    <span class="heading">TrimTable</span>
    <span class="welcome-rule"></span>
    <svg width="22" height="18" viewBox="0 0 22 18"><circle cx="4" cy="4" r="3" fill="none" stroke="#333" stroke-width="1.5"/><circle cx="4" cy="14" r="3" fill="none" stroke="#333" stroke-width="1.5"/><path d="M6.5 5.5L21 14M6.5 12.5L21 4" stroke="#333" stroke-width="1.5"/></svg>
  </div>
  <p class="welcome-text">TrimTable brings together the best hairdressers and barbers in one place. Browse salons in your city, compare treatments and prices, read honest reviews and pick a time that suits you. Booking takes less than a minute and you get an instant confirmation by email. Whether you need a quick trim, a new colour or a full treatment, your next moment of care is only a few clicks away. Salons join us to fill their agenda and reach new guests every day, all without extra effort.</p>
  <a class="cta heading">Get started</a>
</section>

<div class="device" role="img" aria-label="Smartphone showing the TrimTable mobile app"></div>

<footer class="footer">
  <div class="col" style="left:58px">
    <div class="col-title heading">Quick <b>links</b></div>
    <ul class="links"><li>Home</li><li>About Us</li><li>Salons</li><li>Search</li><li>Book</li><li>Contact Us</li></ul>
  </div>
  <div class="col" style="left:160px;width:170px">
    <div class="col-title heading">Contact <b>details</b></div>
    <div class="contact-row"><svg width="10" height="12" viewBox="0 0 10 12"><path d="M5 0C2 0 0 2 0 5c0 3 5 7 5 7s5-4 5-7c0-3-2-5-5-5z" fill="#fff"/></svg><span>Keizersgracht 100<br>1015 Amsterdam, NL</span></div>
    <div class="contact-row"><svg width="10" height="12" viewBox="0 0 10 12"><path d="M2 0h2l1 3-1.5 1a7 7 0 003 3L8 5.5l2 1V9c0 1-1 2-2 2C4 11 0 6 0 2c0-1 1-2 2-2z" fill="#fff"/></svg><span>+31 (0)20 555 0142</span></div>
    <div class="contact-row"><svg width="12" height="10" viewBox="0 0 12 10"><rect width="12" height="9" fill="#fff"/><path d="M0 0l6 5 6-5" fill="none" stroke="#f7941d"/></svg><span>info@trimtable.com</span></div>
  </div>
  <div class="col" style="left:366px">
    <div class="col-title heading">Our <b>gallery</b></div>
    <div class="gallery" role="img" aria-label="Gallery of salon haircut photos"><span></span><span></span><span></span><span></span></div>
    <span class="view-all heading">View all</span>
  </div>
  <div class="col" style="left:492px">
    <div class="col-title heading">Office <b>timings</b></div>
    <dl class="hours">
      <dt>MON-THUR</dt><dd>9:00 AM – 7:00 PM</dd>
      <dt>FRI &amp; SAT</dt><dd>9:00 AM – 6:00 PM</dd>
      <dt>SUN</dt><dd>CLOSED</dd>
    </dl>
  </div>
  <div class="footer-brand"><span class="brand-dot"></span><span class="brand-name">TrimTable</span></div>
</footer>

<div class="bottom-bar">Copyright 2015 TrimTable &nbsp;|&nbsp; All Rights Reserved
  <div class="social"><span></span><span></span><span></span><span></span></div>
</div>

</body>
</html>
```